Satchel & Sundial needs new business card design

I need a new business card design. I'm looking for out-of-the-box design which represents the freedom of being a location independent entrepreneur.
I offer coaching, retreats and trips.
I would like to see designs with and without the photo.
Colors I use are black (#000000), green (#25A796) and brown (#D7C38C)
Website satchelandsundial.example

Target Market(s)

location independent entrepreneurs, digital nomads, people looking to swap the 9 to 5 for a lifestyle business

Industry/Entity Type

Business

Contact Information for Business Card

Dorota Falkner
Your Lifestyle Business Coach, Retreat & Trip Leader
http://satchelandsundial.example
hello@satchelandsundial.example
Live a life you don't need a holiday from

Font styles to use
Serif
Sans Serif

Requirements
Must have
• One side should contain only the logo. I would also consider having the "Live a life you don't need a holiday from" on that side too (depending on how it looks)
• Please show both sides on the designs.

```html
<!DOCTYPE html>
<html lang="en">
<head>
<meta charset="utf-8">
<title>Satchel &amp; Sundial – Business Card</title>
<link rel="stylesheet" href="https://fonts.googleapis.com/css2?family=Oswald:wght@400;500;600&family=Kalam:wght@400&display=swap">
<style>
  :root {
    --ink: #111111;
    --teal: #1f9586;
    --sand: #d4c08a;
    --sand-deep: #c9b47c;
    --paper: #ffffff;
    --paper-shade: #f1f1f1;
    --backdrop: #e6e6e6;
  }
  * { margin: 0; padding: 0; box-sizing: border-box; }
  html, body { width: 1200px; height: 576px; overflow: hidden; }
  body {
    background: var(--backdrop);
    position: relative;
    font-family: "Oswald", "Arial Narrow", sans-serif;
    color: var(--ink);
  }
  .card {
    position: absolute;
    top: 139px;
    width: 485px;
    height: 293px;
    border-radius: 8px;
    overflow: hidden;
  }
  .card--back {
    left: 82px;
    background: linear-gradient(180deg, var(--sand) 0%, var(--sand-deep) 100%);
    display: flex;
    align-items: center;
    justify-content: center;
  }
  .card--front {
    left: 602px;
    background: linear-gradient(180deg, var(--paper) 40%, var(--paper-shade) 100%);
  }
  .wordmark {
    font-family: "Oswald", "Arial Narrow", sans-serif;
    font-weight: 500;
    text-transform: uppercase;
    color: var(--ink);
    letter-spacing: 0.02em;
    white-space: nowrap;
    line-height: 1;
  }
  .card--back .wordmark { font-size: 38px; }
  .card--front .wordmark {
    position: absolute;
    left: 26px;
    top: 32px;
    font-size: 30px;
  }
  .identity {
    position: absolute;
    left: 18px;
    top: 160px;
  }
  .identity__name {
    font-size: 18px;
    font-weight: 600;
    text-transform: uppercase;
    letter-spacing: 0.01em;
    line-height: 1.2;
  }
  .identity__role {
    font-size: 11px;
    font-weight: 400;
    color: var(--teal);
    line-height: 1.3;
  }
  .tagline {
    position: absolute;
    left: 18px;
    top: 236px;
    font-family: "Kalam", cursive;
    font-size: 13px;
    color: var(--teal);
    white-space: nowrap;
  }
  .contacts {
    position: absolute;
    left: 286px;
    top: 180px;
    list-style: none;
    font-size: 11.5px;
    line-height: 1;
  }
  .contacts__item {
    display: flex;
    align-items: center;
    gap: 7px;
    height: 20px;
  }
  .contacts__item--social { margin-top: 19px; color: var(--teal); }
  .contacts__icon { width: 12px; height: 12px; flex: none; }
  .contacts__dot {
    width: 9px; height: 9px; background: var(--ink); border-radius: 1px; flex: none;
    margin-right: 3px;
  }
  .accent { color: var(--teal); }
  .base-band {
    position: absolute;
    left: 0;
    bottom: 3px;
    width: 485px;
    height: 13px;
  }
</style>
</head>
<body>
  <section class="card card--back" aria-label="Card back">
    <div class="wordmark">Satchel &amp; Sundial</div>
  </section>

  <section class="card card--front" aria-label="Card front">
    <div class="wordmark">Satchel &amp; Sundial</div>

    <div class="identity">
      <div class="identity__name">Dorota Falkner</div>
      <div class="identity__role">Your Lifestyle Business Coach</div>
      <div class="identity__role">Retreat &amp; Trip Leader</div>
    </div>

    <p class="tagline">Live a life you don't need a holiday from</p>

    <ul class="contacts">
      <li class="contacts__item">
        <svg class="contacts__icon" viewBox="0 0 12 12" aria-hidden="true">
          <rect x="0.5" y="2" width="11" height="8" fill="var(--teal)"/>
          <path d="M0.5 2 L6 6.5 L11.5 2" fill="none" stroke="#fff" stroke-width="1"/>
        </svg>
        <span>hello@satchelandsundial.example</span>
      </li>
      <li class="contacts__item">
        <svg class="contacts__icon" viewBox="0 0 12 12" aria-hidden="true">
          <circle cx="6" cy="6" r="5.3" fill="none" stroke="var(--teal)" stroke-width="1.2"/>
          <ellipse cx="6" cy="6" rx="2.3" ry="5.3" fill="none" stroke="var(--teal)" stroke-width="1"/>
          <line x1="0.7" y1="6" x2="11.3" y2="6" stroke="var(--teal)" stroke-width="1"/>
        </svg>
        <span>www.<span class="accent">satchelandsundial</span>.example</span>
      </li>
      <li class="contacts__item contacts__item--social">
        <span class="contacts__dot" aria-hidden="true"></span>
        <span>/satchelandsundial</span>
      </li>
    </ul>

    <svg class="base-band" viewBox="0 0 485 13" preserveAspectRatio="none" aria-hidden="true">
      <rect x="0" y="0" width="485" height="13" fill="var(--ink)"/>
      <polygon points="0,0 322,0 322,3 304,13 0,13" fill="var(--teal)"/>
      <polygon points="322,0 336,0 318,13 304,13" fill="#ffffff"/>
    </svg>
  </section>
</body>
</html>
```